Dew and Willow med spa needs an awesome eye catching billboard ad

We need a billboard ad design for a Med Spa with location sin Davenport and Windermere FL A medical spa where the beauty of nature meets the power of science to treat the whole person, mind, body and soul.

Marigold Radiance Med Spa is a medical spa where the beauty of nature meets the power of science to create gorgeous, youthful looking skin. Located in Davenport, Florida, but also serving Four Corners, Celebration, and Windermere, Florida, the talented professional team brings decades of experience in world-class skin care to provide holistic, science-backed aesthetic services and health coaching.

Industry/Entity Type

Spa

Colors
fbee3e
fece3e
eea4c8
e667a6
fbee3d

Requirements
Must have
• Locations in Davenport and Dr Phillips
Phone 407-555-0148
website www.dewandwillow-example.com

Boards for each:
Aesthetic Treatments
Cosmetic Injectables
Quoria facial
add color vs too many earthtones, to catch the eye perhaps using yellow, something that catches the eye and stands out from the normal everyday
Thank you!!!!
Nice to have
• Boards for each:
Aesthetic Treatments
Cosmetic Injectables
Quoria facial
add color vs too many earthtones, to catch the eye
photos that match services,
Thank you!!!!

```html
<!DOCTYPE html>
<html lang="en">
<head>
<meta charset="UTF-8">
<title>Marigold Radiance Med Spa – Cosmetic Injectables Billboard</title>
<link href="https://fonts.googleapis.com/css2?family=Cinzel:wght@400;700&display=swap" rel="stylesheet">
<style>
  :root {
    --page-bg: #ecebe8;
    --board-bg: #fbfbfb;
    --gold: #c9a566;
    --gold-bright: #fece3e;
    --yellow: #fbee3e;
    --gold-soft: #f3dc97;
    --gold-fade: rgba(251, 238, 62, 0);
    --petal: #f6e6b4;
    --ink: #4b4b4e;
    --photo-light: #f3f1ee;
    --photo-mid: #e6ddd2;
  }
  * { margin: 0; padding: 0; box-sizing: border-box; }
  html, body {
    width: 1143px;
    height: 1200px;
    overflow: hidden;
    background: var(--page-bg);
  }
  .billboard {
    position: absolute;
    left: 0;
    top: 457px;
    width: 1143px;
    height: 286px;
    background: var(--board-bg);
    overflow: hidden;
    font-family: "Cinzel", Georgia, serif;
  }
  .petal-decor {
    position: absolute;
    border-radius: 50%;
    background: radial-gradient(circle, var(--petal) 0%, rgba(246, 230, 180, 0.6) 45%, rgba(246, 230, 180, 0) 70%);
  }
  .petal-decor--top-left { left: -40px; top: -40px; width: 170px; height: 170px; }
  .petal-decor--bottom-left { left: -20px; top: 215px; width: 110px; height: 110px; }
  .petal-decor--bottom-mid { left: 760px; top: 235px; width: 100px; height: 100px; }
  .petal-decor--right { left: 1000px; top: -10px; width: 220px; height: 200px; }

  .brand {
    position: absolute;
    left: 190px;
    top: 46px;
    width: 560px;
    display: flex;
    align-items: center;
    justify-content: center;
    gap: 22px;
  }
  .brand__mark {
    width: 34px;
    height: 34px;
    border-radius: 50%;
    background: var(--gold-bright);
    flex: none;
  }
  .brand__text {
    display: flex;
    flex-direction: column;
    align-items: center;
    color: var(--gold);
    font-weight: 400;
    white-space: nowrap;
  }
  .brand__name {
    font-size: 44px;
    line-height: 52px;
    letter-spacing: 9px;
  }
  .brand__tagline {
    font-size: 19px;
    line-height: 26px;
    letter-spacing: 5px;
  }
  .locations {
    position: absolute;
    left: 190px;
    width: 560px;
    top: 145px;
    text-align: center;
    font-size: 13px;
    letter-spacing: 3px;
    color: var(--ink);
  }

  .service-band {
    position: absolute;
    left: 0;
    top: 176px;
    width: 800px;
    height: 50px;
    background: linear-gradient(90deg, var(--gold-bright) 0%, var(--gold-soft) 40%, var(--gold-fade) 100%);
  }
  .service-band__title {
    position: absolute;
    left: 146px;
    top: 0;
    line-height: 50px;
    font-weight: 700;
    font-size: 46px;
    letter-spacing: 3.5px;
    color: var(--ink);
    white-space: nowrap;
  }

  .contact {
    position: absolute;
    left: 60px;
    top: 234px;
    width: 714px;
    height: 44px;
    display: flex;
    align-items: center;
    justify-content: flex-end;
    color: var(--ink);
  }
  .contact__web {
    font-size: 17px;
    letter-spacing: 0.3px;
    white-space: nowrap;
  }
  .contact__divider {
    width: 2px;
    height: 38px;
    background: var(--ink);
    margin: 0 12px;
  }
  .contact__phone {
    font-size: 38px;
    letter-spacing: 0.5px;
    white-space: nowrap;
  }

  .hero-photo {
    position: absolute;
    left: 826px;
    top: 0;
    width: 240px;
    height: 286px;
    background:
      radial-gradient(ellipse 45% 60% at 50% 35%, rgba(199, 154, 104, 0.55) 0%, rgba(199, 154, 104, 0) 70%),
      linear-gradient(180deg, var(--photo-light) 0%, var(--photo-mid) 100%);
  }
</style>
</head>
<body>
  <section class="billboard" aria-label="Marigold Radiance Med Spa cosmetic injectables billboard">
    <div class="petal-decor petal-decor--top-left" role="img" aria-label="Soft cream flower decoration"></div>
    <div class="petal-decor petal-decor--bottom-left" role="img" aria-label="Soft cream flower decoration"></div>
    <div class="petal-decor petal-decor--bottom-mid" role="img" aria-label="Soft cream flower decoration"></div>
    <div class="petal-decor petal-decor--right" role="img" aria-label="Soft cream flower decoration"></div>

    <div class="brand">
      <span class="brand__mark"></span>
      <div class="brand__text">
        <span class="brand__name">MARIGOLD</span>
        <span class="brand__tagline">RADIANCE MED SPA</span>
      </div>
    </div>
    <p class="locations">DAVENPORT · DR PHILLIPS</p>

    <div class="service-band">
      <h1 class="service-band__title">COSMETIC INJECTABLES</h1>
    </div>

    <div class="contact">
      <span class="contact__web">WWW.DEWANDWILLOW-EXAMPLE.COM</span>
      <span class="contact__divider"></span>
      <span class="contact__phone">407-555-0148</span>
    </div>

    <div class="hero-photo" role="img" aria-label="Photo of a smiling woman with long windswept blonde hair in a white top"></div>
  </section>
</body>
</html>
```